Business Card Makeover. Recreate a sleek modern design for our business card.

DO NOT COPY OUR CURRENT DESIGN. MUST BE ONE SIDED BUSINESS CARD.
Create a new business card design, using our new logo. Attached is a sample of our current design and new logo. Please note the address and email will change. The new address is 412 Corvell West Palm Beach 33401 and our website will be www.delmarhollis.example.

We are an architectural and interior design firm. We prefer a clean modern look. Something that is refined and emulates excellence.

Industry/Entity Type

Architecture

Contact Information for Business Card

clean modern look, please do not copy our attached design.

Font styles to use
Other font styles liked:
• see attached business card font

Colors

Designer to choose colors to be used in the design.

Requirements
Must have
• Must have a modern appeal and resemble our current branding.
Nice to have
• modern font, our logo, legible name and titles progressive design
Should not have
• Do not add colors not reflected in our branding. Should not look like our current card.

```html
<!DOCTYPE html>
<html lang="en">
<head>
<meta charset="utf-8">
<title>Delmar Hollis – Business Card</title>
<link href="https://fonts.googleapis.com/css2?family=Lato:wght@400;700&family=Mulish:wght@800&display=swap" rel="stylesheet">
<style>
  :root {
    --backdrop: #232323;
    --card: #ffffff;
    --brand-blue: #0b6fc1;
    --ink: #1e1e1e;
    --wordmark: #2a2a2a;
  }
  * { margin: 0; padding: 0; box-sizing: border-box; }
  html, body {
    width: 1200px; height: 900px; overflow: hidden;
    background: var(--backdrop);
  }
  .card {
    position: absolute;
    left: 445px; top: 199px;
    width: 310px; height: 502px;
    background: var(--card);
    border-radius: 62px 0 62px 0;
    font-family: "Lato", sans-serif;
    color: var(--ink);
  }
  .brand {
    position: absolute; left: 35px; top: 101px;
    display: flex; align-items: center; gap: 10px;
  }
  .brand-dot {
    width: 50px; height: 50px; border-radius: 50%;
    background: var(--brand-blue);
  }
  .brand-name {
    font-family: "Lato", sans-serif;
    font-weight: 400; font-size: 21px; letter-spacing: 0.5px;
    color: var(--wordmark);
  }
  .tagline {
    position: absolute; left: 0; right: 0; top: 157px;
    text-align: center; font-size: 15px;
  }
  .contact { position: absolute; left: 35px; top: 275px; }
  .person-name {
    font-family: "Mulish", sans-serif; font-weight: 800;
    font-size: 18.5px; letter-spacing: 0.4px;
    color: var(--brand-blue); line-height: 22px;
  }
  .person-title { font-size: 14.5px; line-height: 18px; margin-left: 1px; }
  .address { font-size: 14.5px; line-height: 18px; margin-top: 5px; }
  .channels { list-style: none; margin-top: 6px; }
  .channels li {
    display: flex; align-items: center; gap: 4px;
    font-size: 14.5px; line-height: 17px;
  }
  .channels svg { width: 12px; height: 12px; fill: var(--brand-blue); flex: none; }
  .license { font-size: 14.5px; margin-top: 6px; }
  .license-label { color: var(--brand-blue); }
</style>
</head>
<body>
  <article class="card">
    <div class="brand">
      <span class="brand-dot"></span>
      <span class="brand-name">DELMAR HOLLIS</span>
    </div>
    <p class="tagline">Architecture + Interior Design</p>

    <section class="contact">
      <h1 class="person-name">GRAHAM ELLISON</h1>
      <p class="person-title">Partner / Director of Design</p>
      <p class="address">412 Corvell West<br>Palm Beach 33401</p>
      <ul class="channels">
        <li><svg viewBox="0 0 12 12"><path d="M1 4c0-2 2-3 5-3s5 1 5 3l-2 1-1-2H4L3 5zM3 6h6l1 5H2z"/></svg>561.555.0142</li>
        <li><svg viewBox="0 0 12 12"><path d="M3 0h6v12H3zM4 1.5v8h4v-8z"/></svg>561.555.0187</li>
        <li><svg viewBox="0 0 12 12"><path d="M3 0h6v3H3zM0 4h12v5h-2v3H2V9H0zM3 7v4h6V7z"/></svg>561.555.0163</li>
        <li><svg viewBox="0 0 12 12"><path d="M0 2h12v8H0zM1 3l5 4 5-4z"/></svg>graham@delmarhollis.example</li>
        <li><svg viewBox="0 0 12 12"><circle cx="6" cy="6" r="5.5"/><path d="M4 3l2 1-1 2 2 1-1 3" stroke="#fff" stroke-width="1" fill="none"/></svg>www.delmarhollis.example</li>
      </ul>
      <p class="license"><span class="license-label">LIC</span> # AA20004817</p>
    </section>
  </article>
</body>
</html>
```